Ferrowick Groundworks

Need to improve polish and professionalism of PPT presentation. Get consistent look and feel through whole slides, improved look and feel while maintaining the corporate standards/colour scheme, from the Brackwyn corporate presentation. Need everything in Arial font with colours consistent with the PPT template

```html
<!DOCTYPE html>
<html lang="en">
<head>
<meta charset="utf-8">
<title>Ferrowick Groundworks – KPIs &amp; Production Fundamentals</title>
<link href="https://fonts.googleapis.com/css2?family=Arimo:wght@400;700&family=Russo+One&display=swap" rel="stylesheet">
<style>
:root{
  --red:#d22630;
  --deep-red:#c00000;
  --ink:#0c262b;
  --slate:#5b6770;
  --text:#2a2a2a;
  --green:#3d8b26;
  --yellow:#ffff00;
  --purple:#7b1f6f;
  --paper:#ffffff;
}
*{margin:0;padding:0;box-sizing:border-box}
html,body{width:1022px;height:1200px;overflow:hidden;background:var(--paper)}
body{position:relative;font-family:Arimo,Arial,sans-serif;color:var(--text)}
.slide{position:absolute;width:466px;height:262px;background:var(--paper);box-shadow:0 1px 6px rgba(0,0,0,.22);overflow:hidden}
.col-a{left:28px}.col-b{left:526px}
.row-1{top:26px}.row-2{top:313px}.row-3{top:602px}.row-4{top:894px}
.abs{position:absolute}
.title{position:absolute;left:23px;top:15px;font-family:"Russo One",sans-serif;font-size:10px;font-weight:400;color:var(--ink);letter-spacing:.4px;white-space:nowrap}
.title::after{content:"✦";color:var(--red);font-size:7px;position:relative;top:-5px;left:3px}
.marker{position:absolute;left:23px;top:31px;width:20px;height:5px}
.marker::before{content:"";position:absolute;left:0;top:0;width:5px;height:5px;border-radius:50%;background:var(--red)}
.marker::after{content:"";position:absolute;left:7px;top:0;width:12px;height:5px;border-radius:3px;background:linear-gradient(90deg,var(--ink),#6d7a80)}
.brand{position:absolute;right:24px;top:18px;font-family:"Russo One",sans-serif;font-size:10px;color:var(--ink);letter-spacing:.5px}
.footer{position:absolute;left:0;bottom:0;width:100%;height:19px;background:linear-gradient(90deg,var(--red) 0%,#a5222b 22%,var(--ink) 48%,var(--ink) 100%);border-top-left-radius:16px}
.footer .legal{position:absolute;left:23px;top:6px;font-size:5.3px;font-weight:700;color:#fff;white-space:nowrap}
.footer .page{position:absolute;left:424px;top:-3px;width:18px;height:25px}
.footer .page span{position:absolute;left:0;top:9px;width:18px;text-align:center;font-size:4.5px;color:#fff;font-weight:700}
.body7{font-size:7.2px;line-height:10px;color:var(--text);white-space:nowrap}
.tick{color:var(--red);font-weight:700;margin-right:3px}
.pill{position:absolute;background:var(--ink);color:#fff;display:flex;align-items:center;justify-content:center;border-radius:20px;font-family:"Russo One",sans-serif}
.box{position:absolute;color:#fff;display:flex;align-items:center;justify-content:center;text-align:center;border-radius:3px;font-family:"Russo One",sans-serif}
.line{position:absolute;background:var(--slate)}
.photo{position:absolute}
.tum{position:absolute;display:flex;align-items:center;justify-content:center;text-align:center;color:#fff;font-size:7px;line-height:9px;border-radius:3px}
</style>
</head>
<body>

<section class="slide col-a row-1">
  <div class="photo" role="img" aria-label="Four-panel view of terraced open-pit mine benches in red earth under blue sky" style="left:0;top:0;width:466px;height:195px;background:linear-gradient(180deg,#8fb3d8 0%,#b9cfe4 14%,#b4643f 22%,#a0502f 45%,#7c6a5c 65%,#5d5550 100%)"></div>
  <div class="abs" style="left:116px;top:0;width:2px;height:195px;background:#fff"></div>
  <div class="abs" style="left:232px;top:0;width:2px;height:195px;background:#fff"></div>
  <div class="abs" style="left:348px;top:0;width:2px;height:195px;background:#fff"></div>
  <div class="abs" style="left:23px;top:222px;font-family:'Russo One',sans-serif;font-size:17px;color:var(--ink);letter-spacing:.6px">BRACKWYN</div>
  <div class="abs" style="left:205px;top:211px;font-family:'Russo One',sans-serif;font-size:11px;line-height:18px;color:var(--ink);letter-spacing:.3px;white-space:nowrap">FERROWICK GROUNDWORKS KPIS &amp;<br>PRODUCTION FUNDAMENTALS</div>
  <div class="abs" style="left:0;bottom:0;width:466px;height:2px;background:linear-gradient(90deg,var(--red) 0%,var(--red) 45%,var(--ink) 70%)"></div>
</section>

<section class="slide col-b row-1">
  <h2 class="title">KPI &amp; PRODUCTION FUNDAMENTALS</h2>
  <div class="marker"></div>
  <div class="brand">BRACKWYN</div>
  <div class="abs" style="left:23px;top:54px;font-size:5.5px;color:var(--text)">At the end of this module, you will understand</div>
  <div class="abs body7" style="left:23px;top:69px">Understand the key concepts of mine production KPIs</div>
  <div class="abs" style="left:23px;top:87px;font-size:6px;line-height:14.6px;color:var(--text);white-space:nowrap">
    <div><span class="tick">✦</span>Time Usage Model</div>
    <div><span class="tick">✦</span>Availability, Utilization and Productivity</div>
    <div><span class="tick">✦</span>Elements of the haul cycle</div>
    <div><span class="tick">✦</span>Elements of the loading cycle</div>
    <div><span class="tick">✦</span>How changes in each of these elements impact mine production</div>
  </div>
  <div class="abs body7" style="left:23px;top:163px;line-height:14.5px">The goal will be to create a baseline of understanding and a common<br>language across the entire mine-ops team</div>
  <div class="abs body7" style="left:23px;top:197px">You may already understand these concepts</div>
  <div class="abs body7" style="left:23px;top:216px">This is the time to ask questions and get clarification!</div>
  <div class="abs" style="left:291px;top:50px;width:152px;height:174px;background:var(--red);border-radius:6px"></div>
  <div class="photo" role="img" aria-label="Excavator loading a yellow haul truck at a mine site" style="left:295px;top:54px;width:148px;height:170px;border-radius:120px 4px 6px 6px;background:linear-gradient(160deg,#cfdbe6 0%,#b7a06a 40%,#c9a530 60%,#6b6358 100%)"></div>
  <footer class="footer"><span class="legal">© 2024 Brackwyn Mining Solutions Inc. Strictly Confidential</span>
    <div class="page"><svg width="18" height="25" viewBox="0 0 18 25"><path d="M9 0 L11 10 L18 12.5 L11 15 L9 25 L7 15 L0 12.5 L7 10 Z" fill="var(--red)"/></svg><span>02</span></div></footer>
</section>

<section class="slide col-a row-2">
  <h2 class="title">WHAT MAKES UP PRODUCTION</h2>
  <div class="marker"></div>
  <div class="brand">BRACKWYN</div>
  <div class="abs body7" style="left:0;width:466px;text-align:center;top:51px">At its simplest terms, we calculate production like this:</div>
  <div class="pill" style="left:172px;top:71px;width:121px;height:38px;font-size:8.5px">PRODUCTION</div>
  <div class="line" style="left:232px;top:109px;width:1px;height:12px"></div>
  <div class="line" style="left:164px;top:121px;width:139px;height:1px"></div>
  <div class="line" style="left:164px;top:121px;width:1px;height:9px"></div>
  <div class="line" style="left:302px;top:121px;width:1px;height:9px"></div>
  <div class="box" style="left:106px;top:130px;width:117px;height:28px;background:var(--slate);font-size:7px">Equipment Productivity</div>
  <div class="box" style="left:244px;top:130px;width:117px;height:28px;background:var(--slate);font-size:7px">Operating Time</div>
  <div class="abs body7" style="left:0;width:466px;text-align:center;top:170px">This is true for any process:</div>
  <div class="abs body7" style="left:89px;width:100px;text-align:center;top:190px;color:var(--red)">Mowing the lawn</div>
  <div class="abs body7" style="left:184px;width:100px;text-align:center;top:190px;color:var(--red)">Driving</div>
  <div class="abs body7" style="left:278px;width:100px;text-align:center;top:190px;color:var(--red)">Mine Production</div>
  <div class="abs body7" style="left:0;width:466px;text-align:center;top:212px">Production goes up or down because of a change in <b>Equipment Productivity</b> or <b>Operating Time</b></div>
  <footer class="footer"><span class="legal">© 2024 Brackwyn Mining Solutions Inc. Strictly Confidential</span>
    <div class="page"><svg width="18" height="25" viewBox="0 0 18 25"><path d="M9 0 L11 10 L18 12.5 L11 15 L9 25 L7 15 L0 12.5 L7 10 Z" fill="var(--red)"/></svg><span>03</span></div></footer>
</section>

<section class="slide col-b row-2">
  <h2 class="title">WHAT MAKES UP PRODUCTION</h2>
  <div class="marker"></div>
  <div class="brand">BRACKWYN</div>
  <div class="abs body7" style="left:24px;top:58px">At its simplest terms, we calculate production like this:</div>
  <div class="pill" style="left:76px;top:84px;width:96px;height:30px;font-size:7px">PRODUCTION</div>
  <div class="line" style="left:124px;top:114px;width:1px;height:21px"></div>
  <div class="line" style="left:69px;top:135px;width:111px;height:1px"></div>
  <div class="line" style="left:69px;top:135px;width:1px;height:20px"></div>
  <div class="line" style="left:179px;top:135px;width:1px;height:20px"></div>
  <div class="box" style="left:24px;top:155px;width:93px;height:23px;background:var(--slate);font-size:5.5px">Equipment Productivity</div>
  <div class="box" style="left:133px;top:155px;width:93px;height:23px;background:var(--red);font-size:5.5px">Operating Time</div>
  <div class="abs body7" style="left:23px;top:195px;line-height:14.5px"><span class="tick">✔</span>Operating time is the time when a piece of equipment<br>is performing it’s primary function</div>
  <div class="abs" style="left:245px;top:60px;width:1px;height:157px;background:#d5d5d5"></div>
  <div class="abs body7" style="left:259px;top:59px;line-height:14.5px"><span class="tick">✔</span>To better understand, communicate and discuss<br>the different categories of how we calculate operating<br>time, we use something called a Time Usage Model</div>
  <div class="abs body7" style="left:259px;top:121px;line-height:14.5px"><span class="tick">✔</span>Each industry has its own time usage model, and<br>they can vary slightly from industry to industry</div>
  <div class="abs body7" style="left:259px;top:176px;line-height:14.5px"><span class="tick">✔</span>Even within an industry, (e.g. Mining) a Time Usage<br>Model can vary from operation to operation</div>
  <footer class="footer"><span class="legal">© 2024 Brackwyn Mining Solutions Inc. Strictly Confidential</span>
    <div class="page"><svg width="18" height="25" viewBox="0 0 18 25"><path d="M9 0 L11 10 L18 12.5 L11 15 L9 25 L7 15 L0 12.5 L7 10 Z" fill="var(--red)"/></svg><span>04</span></div></footer>
</section>

<section class="slide col-a row-3">
  <h2 class="title">GENERIC TIME USAGE MODEL</h2>
  <div class="marker"></div>
  <div class="brand">BRACKWYN</div>
  <div class="tum" style="left:24px;top:58px;width:418px;height:24px;background:var(--slate)">Calendar Time</div>
  <div class="tum" style="left:24px;top:83px;width:272px;height:24px;background:var(--slate)">Available Time</div>
  <div class="tum" style="left:298px;top:83px;width:144px;height:73px;background:var(--deep-red);display:block">
    <div style="height:12px;font-size:5px;line-height:12px;border-bottom:1px solid #e06a6a">Down</div>
    <div style="display:flex;height:61px">
      <div style="flex:1;display:flex;align-items:center;justify-content:center;border-right:1px solid #e06a6a;font-size:6.5px">Unscheduled</div>
      <div style="flex:1;display:flex;align-items:center;justify-content:center;font-size:6.5px">Scheduled</div>
    </div>
  </div>
  <div class="tum" style="left:24px;top:108px;width:151px;height:24px;background:var(--slate)">Operating Time</div>
  <div class="tum" style="left:176px;top:108px;width:60px;height:48px;background:var(--green)">Operating<br>Delay</div>
  <div class="tum" style="left:237px;top:108px;width:58px;height:48px;background:var(--yellow);color:#222">Standby<br>Time</div>
  <div class="tum" style="left:24px;top:133px;width:78px;height:24px;background:var(--slate)">Effective Time</div>
  <div class="tum" style="left:104px;top:133px;width:71px;height:24px;background:var(--purple)">Non-Effective Time</div>
  <div class="abs body7" style="left:23px;top:176px"><span class="tick">✔</span>This is a generic Mining time usage model</div>
  <div class="abs body7" style="left:23px;top:195px;line-height:14.5px"><span class="tick">✔</span>There may be variations from mine-to-mine (ie Utilized time vs Operating Time) but this model describes everything<br>mine operations needs to know about the time usage of a piece of equipment</div>
  <footer class="footer"><span class="legal">© 2024 Brackwyn Mining Solutions Inc. Strictly Confidential</span>
    <div class="page"><svg width="18" height="25" viewBox="0 0 18 25"><path d="M9 0 L11 10 L18 12.5 L11 15 L9 25 L7 15 L0 12.5 L7 10 Z" fill="var(--red)"/></svg><span>05</span></div></footer>
</section>

<section class="slide col-b row-3">
  <h2 class="title">TUM – CALENDAR TIME</h2>
  <div class="marker"></div>
  <div class="brand">BRACKWYN</div>
  <div class="pill" style="left:64px;top:64px;width:338px;height:32px;font-family:Arimo,Arial,sans-serif;font-size:9px">CALENDAR TIME</div>
  <div class="abs" style="left:0;width:466px;text-align:center;top:120px;font-size:12px;color:#111">Calendar time means all the time in a period</div>
  <div class="abs" style="left:0;width:466px;text-align:center;top:153px;font-size:7px;line-height:20.3px;color:#111">
    Calendar time for 1 Year = 365 Days<br>Calendar time for October = 31 days<br>Calendar time for 1 shift = 12 hours
  </div>
  <footer class="footer"><span class="legal">© 2024 Brackwyn Mining Solutions Inc. Strictly Confidential</span>
    <div class="page"><svg width="18" height="25" viewBox="0 0 18 25"><path d="M9 0 L11 10 L18 12.5 L11 15 L9 25 L7 15 L0 12.5 L7 10 Z" fill="var(--red)"/></svg><span>06</span></div></footer>
</section>

<section class="slide col-a row-4">
  <h2 class="title">OVERVIEW – SIC &amp; VISUAL MANAGEMENT</h2>
  <div class="marker"></div>
  <div class="brand">BRACKWYN</div>
  <div class="abs body7" style="left:23px;top:59px"><span class="tick">✔</span>Dispatchers and Pit Supervisors use the SIC tool to monitor the real-time performance of the truck and shovel fleet.</div>
  <div class="abs body7" style="left:23px;top:93px;line-height:14.5px"><span class="tick">✔</span>The tool is monitored hourly to identify underperformance. The dispatcher may be the lead in identifying actions<br>&nbsp;for the Pit Supervisor</div>
  <div class="abs body7" style="left:23px;top:136px;line-height:14.5px"><span class="tick">✔</span>Once opportunities or underperforming areas are identified Dispatchers and Supervisors will take collaborative action<br>&nbsp;to address them</div>
  <div class="abs body7" style="left:23px;top:185px;line-height:14.5px"><span class="tick">✔</span>The Visual Management process is an accountability check and information share. ‘Did we monitor the SIC,<br>&nbsp;communicate opportunities and take action during the shift?’</div>
  <footer class="footer"><span class="legal">© 2024 Brackwyn Mining Solutions Inc. Strictly Confidential</span>
    <div class="page"><svg width="18" height="25" viewBox="0 0 18 25"><path d="M9 0 L11 10 L18 12.5 L11 15 L9 25 L7 15 L0 12.5 L7 10 Z" fill="var(--red)"/></svg><span>07</span></div></footer>
</section>

<section class="slide col-b row-4">
  <h2 class="title">VISUAL MANAGEMENT</h2>
  <div class="marker"></div>
  <div class="brand">BRACKWYN</div>
  <div class="abs body7" style="left:23px;top:51px;font-weight:700">Expectations @ Visual Management Meeting – Dispatchers &amp; Supervisors</div>
  <div class="abs body7" style="left:23px;top:71px"><span class="tick">✔</span>For each KPI they are accountable for Dispatcher and Supervisors must report:</div>
  <div class="abs" style="left:23px;top:91px;font-size:6.2px;line-height:14.5px;color:var(--text);white-space:nowrap">
    What happened during the shift - Good, bad and changes in KPI<br>When were issues identified<br>What communication &amp; actions did you take<br>Did it improve<br>How will KPI look going forward<br>Any other actions required
  </div>
  <div class="abs body7" style="left:23px;top:189px;line-height:14.5px;font-weight:700">If you are monitoring the SIC during the shift it is easy to answer<br>these questions</div>
  <div class="abs" style="left:311px;top:51px;width:132px;height:172px;background:var(--red);border-radius:6px"></div>
  <div class="photo" role="img" aria-label="Two mine workers in hard hats and orange vests viewed from behind near heavy equipment" style="left:311px;top:55px;width:128px;height:168px;border-radius:90px 4px 6px 6px;background:linear-gradient(170deg,#7d8e9a 0%,#a8893f 35%,#e0742a 65%,#3d3c3a 100%)"></div>
  <footer class="footer"><span class="legal">© 2024 Brackwyn Mining Solutions Inc. Strictly Confidential</span>
    <div class="page"><svg width="18" height="25" viewBox="0 0 18 25"><path d="M9 0 L11 10 L18 12.5 L11 15 L9 25 L7 15 L0 12.5 L7 10 Z" fill="var(--red)"/></svg><span>08</span></div></footer>
</section>

</body>
</html>
```